Website Design for a different kind of Business Consulting organisation needed!

We need a website design that reflects who we are, the simplicity of our consulting business and with a focus on our priority - to help our clients deliver, or execute - the "e" in Vantor-i.

Our key high level requirements are:
1) Simple and intuitive look and feel
2) Integration with all key social media platforms, twitter, facebook, linkedin, tumblr.

10 pages, tops.
- Main page - Welcome
- About Us/ Who are Vantor-i?
- 5 services pages - Project Management, Business Process Management, Change Management, Business Analysis and Finance Systems
- Contact Us

Something like:
http://www.lumvexhold.example/

Vantor-i is a registered trademark and all Logos and other branded material are attached for reference.

So, what’s our gig: A few snippets from previous work...

We are a different kind of business consulting group. We partner with our clients to help them deliver change. We don't just provide them with the theory. We also provide them with the leadership and capability to execute the change.

We aren’t a one stop shop, and we don’t offer cookie cutter solutions. We’re a boutique consulting firm covering Project Management, Business Process Management, Change Management and Business Analytics.

Vantor-i is a professional services organisation that partners with their clients to lead the execution of strategic process and system improvement initiatives. Vantor-i combines hands on delivery with coaching in best practice methodologies and approaches to build their clients capabilities to ensure their ongoing success in project implementations.

UPDATES:

Thanks to everyone who has submitted designs so far. The standard of designs coming through is quite high, with lots of professional designs that nail the design brief. Eliminating them is proving to be quite challenging.

A few updates to the job brief:
- Please make sure the design fits on one page. We would like all of our information to be on the first page that people see without them having to scroll down
- Please ensure you include the FIVE services we offer in the design
- Please use corporate images/istock photos in your designs which are relevant to our business
- Please add a section for a live twitter feed from our twitter account and a link to google+
- Please add a section for news/updates

Also, if you are able to build a site once a design is selected, please let us know.

Thanks,

Maribel.

Target Market(s)

Our target customers are large enterprises in Australia that are growing rapidly and have recently (last 24 months) undertaken or are currently undergoing software implementations and business process improvement programs. These businesses have a turnover of $100m or above and are working hard to differentiate themselves from their competitors but are not seeing the return on investment promised by software vendors and process improvement initiatives.

Industry/Entity Type

Leadership

Requirements
Must have
• Collaboration / Training / Workshop / Consulting images all of a professional nature.
Simple, non-cluttered look with plenty of white space.

```html
<!DOCTYPE html>
<html lang="en">
<head>
<meta charset="utf-8">
<title>Vantor-i — Business Consulting</title>
<link href="https://fonts.googleapis.com/css2?family=PT+Sans:wght@400;700&family=Open+Sans:wght@400;600&family=Roboto+Condensed:wght@300;400&display=swap" rel="stylesheet">
<style>
  :root{
    --blue:#0b5bb5;
    --blue-dark:#0a4f9e;
    --nav-top:#1a6fc9;
    --nav-bottom:#0b55ab;
    --text:#555;
    --heading:#333;
    --rule:#dcdcdc;
    --band:#ececec;
    --footer:#555555;
    --footer-bottom:#4d4d4d;
    --footer-text:#e6e6e6;
    --footer-rule:#6c6c6c;
  }
  *{margin:0;padding:0;box-sizing:border-box}
  html,body{width:808px;height:1200px;overflow:hidden;background:#fff}
  body{position:relative;font-family:"Open Sans",Arial,sans-serif;color:var(--text)}
  .abs{position:absolute}

  /* header */
  .brand{left:92px;top:20px;font-family:"PT Sans",sans-serif;font-size:25px;color:var(--blue);letter-spacing:.5px}
  .search{left:580px;top:27px;width:134px;height:19px;background:#ececec;border-radius:3px;font-size:7px;color:#777;padding:5px 9px}
  .search svg{position:absolute;right:9px;top:4px}

  .nav{left:86px;top:74px;width:635px;height:30px;background:linear-gradient(var(--nav-top),var(--nav-bottom));border-bottom:2px solid #0a4a95;display:flex;padding-left:4px}
  .nav a{color:#fff;text-decoration:none;font-family:Arial,sans-serif;font-size:8.8px;height:28px;line-height:28px;padding:0 19px;border-right:1px solid rgba(0,0,0,.18);box-shadow:1px 0 0 rgba(255,255,255,.12)}
  .nav a:last-child{border:0;box-shadow:none}

  /* hero */
  .hero{left:87px;top:114px;width:634px;height:236px;background:linear-gradient(100deg,#dfe6ee 0%,#c9d5e2 40%,#aec3da 60%,#d4dde8 100%)}
  .hero-title{left:458px;top:146px;font-family:"PT Sans",sans-serif;font-size:13.2px;line-height:22px;color:var(--blue)}
  .hero-title b{font-size:16px;font-weight:400}
  .dots{left:385px;top:361px;display:flex;gap:3px}
  .dots i{width:5px;height:5px;border-radius:50%;background:#999}
  .dots i:first-child{background:var(--blue)}

  h2.section{font-family:"PT Sans",sans-serif;font-weight:400;font-size:16.5px;color:var(--heading);border-bottom:1px solid var(--rule);padding-bottom:6px}
  .copy{font-size:7.4px;line-height:13.6px;text-align:justify;color:var(--text)}

  .welcome-title{left:87px;top:385px;width:374px}
  .welcome-photo{left:87px;top:428px;width:99px;height:67px;border:1px solid #ddd;background:linear-gradient(135deg,#eef2f7,#c7d3e0 60%,#9fb2c8)}
  .welcome-text{left:199px;top:425px;width:262px}
  .welcome-more{left:87px;top:515px;width:374px}

  .news-title{left:494px;top:382px;width:227px;padding-bottom:9px}
  .news-item{left:494px;width:227px}
  .news-item .date{color:var(--blue);font-size:7.6px;line-height:12px}
  .news-item p{text-align:left}
  .news-sep{left:494px;top:486px;width:215px;border-top:1px dotted #ccc}

  .btn{background:var(--blue-dark);color:#fff;font-family:Verdana,sans-serif;font-weight:700;font-size:7.6px;display:flex;align-items:center;justify-content:center;height:20px;width:81px}

  .services-title{left:87px;top:596px;width:634px}
  .service{top:638px;width:139px}
  .service .photo{width:139px;height:68px;border:1px solid #d6d6d6;box-shadow:0 1px 2px rgba(0,0,0,.15);padding:3px;background:#fff}
  .service .photo div{width:100%;height:100%}
  .service h3{font-family:"PT Sans",sans-serif;font-weight:400;font-size:16px;color:var(--blue);margin-top:10px;padding-bottom:4px;border-bottom:1px solid var(--rule)}
  .service .copy{margin-top:7px;height:80px}
  .service .btn{margin-left:58px;margin-top:18px}

  .partners{left:0;top:916px;width:808px;height:61px;background:var(--band);display:flex;align-items:center;justify-content:space-between;padding:0 92px}
  .partners span{font-family:"PT Sans",sans-serif;font-weight:700;font-size:13px;color:#5e5e5e}

  .footer{left:0;top:977px;width:808px;height:188px;background:var(--footer)}
  .footer-bar{left:0;top:1165px;width:808px;height:35px;background:var(--footer-bottom)}
  .footer h4{font-family:"Roboto Condensed",sans-serif;font-weight:300;font-size:15px;color:#fff;position:absolute}
  .footer .ftext{font-size:7.6px;line-height:13.6px;color:var(--footer-text);position:absolute}
  .pages-list{left:88px;top:48px;width:137px;list-style:none;position:absolute}
  .pages-list li{font-size:7.8px;color:var(--footer-text);height:20.2px;line-height:20px;border-bottom:1px solid var(--footer-rule)}
  .social{position:absolute;left:253px;top:149px;display:flex;gap:5px}
  .social i{width:22px;height:22px;border-radius:4px;display:block}
  .copyright{left:88px;top:1176px;font-size:7.8px;color:var(--footer-text)}
  .to-top{left:662px;top:1175px;font-size:7.8px;color:var(--footer-text)}
</style>
</head>
<body>

<header>
  <div class="abs brand">Vantor-i</div>
  <div class="abs search">Search
    <svg width="14" height="11" viewBox="0 0 14 11"><circle cx="5" cy="4.5" r="3.3" fill="none" stroke="#1d5fb0" stroke-width="1.6"/><line x1="7.5" y1="6.5" x2="12.5" y2="10" stroke="#1d5fb0" stroke-width="2"/></svg>
  </div>
  <nav class="abs nav">
    <a>Home</a><a>About Us</a><a>Services</a><a>Portfolio</a><a>Blog</a><a>Contact Us</a>
  </nav>
</header>

<div class="abs hero" role="img" aria-label="Photo of two young business professionals in front of a blue digital data interface"></div>
<div class="abs hero-title"><b>E</b>xecution of strategic<br>Process &amp; System improvement initiatives</div>
<div class="abs dots"><i></i><i></i><i></i><i></i></div>

<section>
  <h2 class="abs section welcome-title">Welcome to Vantor-i</h2>
  <div class="abs welcome-photo" role="img" aria-label="Photo of a businesswoman working at a laptop"></div>
  <p class="abs copy welcome-text">Consectetur adipiscing elit. Cras in leo at sapien varius tristique. Ut dapibus sodales libero a malesuada. Aenean ullamcorper convallis lorem at hendrerit. Nam vel arcu lacus. Cras dapibus egestas mi in porttitor. Vestibulum massa metus, vestibulum non consectetur vel, congue ullamcorper sapien. Aenean semper aliquet leo, in posuere justo faucibus eget. Proin pulvinar risus libero, non ullamcorper nulla.</p>
  <p class="abs copy welcome-more">Nullam hendrerit dui eget orci luctus sed porta odio feugiat. Duis turpis nisi, suscipit quis pretium nec, cursus sed turpis. Phasellus quis risus id felis vestibulum eleifend. Vivamus sed augue justo. Lorem ipsum dolor sit amet, consectetur adipiscing elit.</p>
</section>

<section>
  <h2 class="abs section news-title">Vantor-i News</h2>
  <div class="abs news-item" style="top:426px">
    <div class="date">28/02/14</div>
    <p class="copy">The service offering ranges across contingent permanent recruitment, contract placements, Visa Solutions, managed services and retained search.</p>
  </div>
  <div class="abs news-sep"></div>
  <div class="abs news-item" style="top:497px">
    <div class="date">12/03/14</div>
    <p class="copy">We are guided by 5 key values - collaboration, unity, rigour, accountability and continual improvement. These values unite our team of almost 50, and inspire us to go beyond our expectations</p>
  </div>
  <div class="abs btn" style="left:640px;top:574px">Read More</div>
</section>

<section>
  <h2 class="abs section services-title">Our Services</h2>

  <article class="abs service" style="left:87px">
    <div class="photo"><div role="img" aria-label="Photo of a team gathered around a meeting table from above" style="background:linear-gradient(135deg,#5b5650,#c9c2b6 55%,#e4ddd2)"></div></div>
    <h3>Mauris egestas</h3>
    <p class="copy">Lorem ipsum dolor sit a, consectetur adipiscing elit. Fusce convallis adipiscing turpis, vel adipiscing sem ultrices vel. Vivamus faucibus massa nunc. Phasellus gravida aliquam ante, non pulvinar orci. auctor in.</p>
    <div class="btn">Read More</div>
  </article>

  <article class="abs service" style="left:252px">
    <div class="photo"><div role="img" aria-label="Photo of a woman drawing a rising graph line" style="background:linear-gradient(120deg,#c9a88e,#f1f1f1 55%,#dfe7f2)"></div></div>
    <h3>Donec sit amet</h3>
    <p class="copy">Lorem ipsum dolor sit a, consectetur adipiscing elit. Fusce convallis adipiscing turpis, vel adipiscing sem ultrices vel. Vivamus faucibus massa nunc. Phasellus gravida aliquam ante, non pulvinar orci auctor in.</p>
    <div class="btn">Read More</div>
  </article>

  <article class="abs service" style="left:417px">
    <div class="photo"><div role="img" aria-label="Photo of a business team in a meeting room" style="background:linear-gradient(180deg,#dfe5ec,#8c97a6 55%,#2e3440)"></div></div>
    <h3>Pellentesque</h3>
    <p class="copy">Lorem ipsum dolor sit a, consectetur adipiscing elit. Fusce convallis adipiscing turpis, vel adipiscing sem ultrices vel. Vivamus faucibus massa nunc. Phasellus gravida aliquam ante, non pulvinar orci auctor in.</p>
    <div class="btn">Read More</div>
  </article>

  <article class="abs service" style="left:582px">
    <div class="photo"><div role="img" aria-label="Photo of a businesswoman beside a growing bar chart" style="background:linear-gradient(90deg,#f3f3f3,#d9d4cf 45%,#7a6f68)"></div></div>
    <h3>Aliquam semper</h3>
    <p class="copy">Lorem ipsum dolor sit a, consectetur adipiscing elit. Fusce convallis adipiscing turpis, vel adipiscing sem ultrices vel. Vivamus faucibus massa nunc. Phasellus gravida aliquam ante, non pulvinar orci auctor in.</p>
    <div class="btn">Read More</div>
  </article>
</section>

<div class="abs partners">
  <span>Kovra</span><span>Brightlane &amp; Co</span><span>Tallow</span><span>Mersey Group</span><span>Quorin</span><span>Halvette</span><span>Dunmark</span>
</div>

<footer class="abs footer">
  <h4 style="left:88px;top:16px">Pages</h4>
  <ul class="pages-list">
    <li>» Home</li><li>» About Us</li><li>» Services</li><li>» Portfolio</li><li>» Blog</li><li>» Contact Us</li>
  </ul>

  <h4 style="left:252px;top:16px">About Us</h4>
  <p class="ftext" style="left:252px;top:47px;width:305px">Lorem ipsum dolor sit amet, consectetur adipiscing elit. Morbi ultricies gravida enim. In nulla enim, blandit vel, lacinia a, congue eu, turpis. Donec ut nisi. Curabitur a odio eu mi dapibus porttitor. more about us »</p>
  <p class="ftext" style="left:252px;top:101px">Be our guest at the blog, services, portfolio pages.</p>

  <h4 style="left:251px;top:123px">Keep in Touch</h4>
  <div class="social">
    <i role="img" aria-label="Social link 1" style="background:#5ab7dc"></i>
    <i role="img" aria-label="Social link 2" style="background:#3b5b96"></i>
    <i role="img" aria-label="Feed link" style="background:#e07a2c"></i>
    <i role="img" aria-label="Social link 4" style="background:#e9e9e9"></i>
    <i role="img" aria-label="Social link 5" style="background:#1f6fa8"></i>
  </div>

  <h4 style="left:581px;top:16px">Contact Info</h4>
  <p class="ftext" style="left:581px;top:47px">Phone: +123456789<br>Fax: +123456789<br>E-mail: name@vantor-i.com<br>Or fill out form on Contact page</p>
</footer>
<div class="abs footer-bar"></div>
<div class="abs copyright">Copyright © 2014, vantor-i . All rights reserved.</div>
<div class="abs to-top">Back to Top ▴</div>

</body>
</html>
```